Video Editing Website - Wordpress Design Project

Hi There
I am setting up a Tribute Funeral Video and Home Video Editing Website for my Company. "Reel Harbor". This is to assist people with putting together their Videos and Photos with music to show at a Funeral or for Family Memories. I already have a domain www.reelharbor.com.au, but I have no host yet.

Some websites that already do this are http://www.quietlantern.com.au/tributes, http://www.cobaltframeworks.com.au/services/funeral-tribute-videos.html, and http://www.sundialkeepsakes.com.au/
These are examples not to cpy, but to get an idea of what I am offering so you can design accordingly.

I have a logo which is attached. You will see that the logo is mainly blue, so I would appreciate a website with that colour on the pages, but not ALL over the page.

I would like to upload videos occasionally from clipnest.com so I would appreciate that option incorporated.

Thank you lots.
Gareth

Target Market(s)

Families predominately in the 25-60 age range

Industry/Entity Type

It Company

Requirements
Must have
• *Ability to upload Videos from clipnest.com
*Ability for me to edit the content whenever I need to
*A contact page to send email messages to me

```html
<!DOCTYPE html>
<html lang="en">
<head>
<meta charset="utf-8">
<title>Reel Harbor</title>
<link rel="stylesheet" href="https://fonts.googleapis.com/css2?family=Source+Sans+3:wght@400;600;700&family=Arimo:wght@400;700&display=swap">
<style>
:root{
  --navy:#161a6e;
  --navy-deep:#0c1060;
  --nav-top:#2e4fb0;
  --nav-bottom:#0b1a78;
  --logo-blue:#1f3f9a;
  --ink:#222;
  --line:#cfcfcf;
  --footer-top:#5b5b5b;
  --footer-bottom:#2b2b2b;
  --btn-top:#5aa3dc;
  --btn-bottom:#2a5e8c;
}
*{margin:0;padding:0;box-sizing:border-box}
html,body{width:984px;height:1200px;overflow:hidden;background:#fff}
body{position:relative;font-family:"Source Sans 3",sans-serif;color:var(--ink)}
.abs{position:absolute}
.top-bar{left:0;top:0;width:984px;height:7px;background:#2d2d2d}

.brand{left:118px;top:82px;display:flex;align-items:center;gap:7px}
.brand-mark{width:16px;height:16px;border-radius:50%;background:var(--logo-blue)}
.brand-name{font-size:26px;font-weight:400;color:var(--logo-blue);line-height:1;letter-spacing:-.3px}

.search{left:674px;top:54px;width:193px;height:30px;border:1px solid #c8c8c8;border-radius:6px;background:linear-gradient(#fff,#f1f1f1);font-family:Arimo,sans-serif;font-size:10px;color:#333;padding:9px 0 0 11px}
.search svg{position:absolute;right:10px;top:8px}

.main-nav{left:114px;top:133px;width:754px;height:39px;border-radius:4px;background:linear-gradient(var(--nav-top),var(--nav-bottom));display:flex}
.main-nav span{display:flex;align-items:center;justify-content:center;color:#fff;font-weight:700;font-size:12px;height:100%;border-right:1px solid rgba(255,255,255,.25)}
.main-nav span:last-child{border-right:none}

.hero{left:114px;top:183px;width:755px;height:300px;border:1px solid var(--line)}
.hero-photo{position:absolute;inset:1px;background:linear-gradient(90deg,#c98a6a 0%,#8a90c8 30%,#9db45a 55%,#c9d57c 80%,#a9bf5c 100%)}
.hero-title{left:526px;top:268px;font-family:Arimo,sans-serif;font-size:26px;color:var(--navy);letter-spacing:.5px}
.hero-quote{left:452px;top:329px;width:410px;font-size:17px;line-height:24px;color:#111}
.dots{left:564px;top:452px;display:flex;gap:11px}
.dots i{width:12px;height:12px;border-radius:50%;background:#6b6b6b;display:block}
.dots i:first-child{background:var(--navy)}

.section-title{font-size:14px;font-weight:700;color:var(--navy)}
.welcome-text{left:118px;top:539px;width:550px;font-size:10px;line-height:20px;color:#222}
.upload-btn{left:709px;top:536px;width:157px;height:50px;border-radius:3px;background:linear-gradient(var(--btn-top),var(--btn-bottom));color:#fff;font-family:Arimo,sans-serif;font-weight:700;font-size:13px;display:flex;align-items:center;justify-content:center}

.video{left:118px;top:677px;width:336px;height:195px;border:2px solid #d6d6d6}
.video-photo{position:absolute;inset:0;background:linear-gradient(160deg,#6f8a4e 0%,#3a3148 45%,#8b6fa0 55%,#6d8a4a 100%)}
.play{position:absolute;left:138px;top:67px}

.testi-photo{top:677px;width:156px;height:88px;border:1px solid #bbb;background:linear-gradient(90deg,#3c3c3c,#9a9a9a,#d8d8d8)}
.testi-text{top:786px;width:156px;font-family:Arimo,sans-serif;font-size:10px;line-height:15.5px;color:#444}
.read-more{top:854px;width:68px;height:24px;border-radius:3px;background:var(--navy-deep);color:#fff;font-family:Arimo,sans-serif;font-size:9.5px;display:flex;align-items:center;justify-content:center}

.gallery-item{top:960px;width:142px;height:110px;border:1px solid #ccc}

.footer{left:0;top:1111px;width:984px;height:89px;background:linear-gradient(var(--footer-top),var(--footer-bottom))}
.footer-links{left:116px;top:1134px;color:#fff;font-size:10px;font-weight:700}
.copyright{left:116px;top:1159px;color:#fff;font-size:9px;font-weight:600}
.social{left:764px;top:1143px;display:flex;gap:5px}
.social i{display:block;width:22px;height:22px;border-radius:50%;border:2px solid #fff}
</style>
</head>
<body>
<div class="abs top-bar"></div>

<div class="abs brand"><span class="brand-mark"></span><span class="brand-name">reelharbor</span></div>

<div class="abs search">Search
  <svg width="13" height="13" viewBox="0 0 13 13"><circle cx="5" cy="5" r="3.6" fill="none" stroke="#222" stroke-width="2"/><line x1="7.5" y1="7.5" x2="11.5" y2="11.5" stroke="#222" stroke-width="2.6" stroke-linecap="round"/></svg>
</div>

<nav class="abs main-nav">
  <span style="width:123px">HOME</span>
  <span style="width:112px">ABOUT</span>
  <span style="width:117px">SERVICES</span>
  <span style="width:135px">RESOURCES</span>
  <span style="width:140px">CONTACT US</span>
  <span style="width:127px">SYDNEY</span>
</nav>

<div class="abs hero">
  <div class="hero-photo" role="img" aria-label="Smiling older couple on a bicycle in a sunny leafy park"></div>
</div>
<div class="abs hero-title">REEL HARBOR</div>
<div class="abs hero-quote">"On the other hand, we denounce with righteous indig-nation and &nbsp; by the charms of pleasure of the moment,</div>
<div class="abs dots"><i></i><i></i><i></i><i></i></div>

<h2 class="abs section-title" style="left:117px;top:504px">WELCOME TO OUR COMPANY</h2>
<p class="abs welcome-text">"On the other hand, we denounce with righteous indignation and dislike men who are so beguiled and demoralized by the charms of pleasure of the moment, so blinded by desire, that they cannot foresee the pain and trouble that are bound to ensue; and equal blame belongs to those who fail in their duty through weakness of will, which is the same as saying through shrinking from toil and pain. These cases are perfectly simple and easy to distinguish.</p>
<div class="abs upload-btn">UPLAOD VIDEOS</div>

<h2 class="abs section-title" style="left:116px;top:634px">TRIBUTE FUNERAL VIDEO</h2>
<h2 class="abs section-title" style="left:636px;top:639px">TESTIMONIALS</h2>

<div class="abs video">
  <div class="video-photo" role="img" aria-label="Flower-covered casket resting on lowering straps above a grave"></div>
  <svg class="play" width="36" height="36" viewBox="0 0 36 36"><circle cx="18" cy="18" r="16" fill="#555" fill-opacity=".8" stroke="#ddd" stroke-width="2"/><path d="M14 10 L26 18 L14 26 Z" fill="#eee"/></svg>
</div>

<div class="abs testi-photo" style="left:520px" role="img" aria-label="Black and white photo of an elderly man with a child"></div>
<div class="abs testi-photo" style="left:712px" role="img" aria-label="Black and white photo of a mother with her baby"></div>
<p class="abs testi-text" style="left:522px">Lorem ipsum dolor sit amet, con-sectetuer adipiscing elit. Nndimen-tum at, laoreet mattis, massa.</p>
<p class="abs testi-text" style="left:714px">Lorem ipsum dolor sit amet, con-sectetuer adipiscing elit. Nndimen-tum at, laoreet mattis, massa.</p>
<div class="abs read-more" style="left:521px">READ MORE</div>
<div class="abs read-more" style="left:714px;top:855px">READ MORE</div>

<h2 class="abs section-title" style="left:440px;top:909px">PHOTO GALLERY</h2>
<svg class="abs" style="left:845px;top:924px" width="24" height="13" viewBox="0 0 24 13"><path d="M8 0 L0 6.5 L8 13 Z" fill="#555"/><path d="M15 0 L23 6.5 L15 13 Z" fill="#555"/></svg>

<div class="abs gallery-item" style="left:114px;background:linear-gradient(90deg,#1a1a1a,#3a3a3a,#8a2a2a)" role="img" aria-label="Mourner holding a red rose beside a casket"></div>
<div class="abs gallery-item" style="left:267px;background:linear-gradient(#fff,#f2ecd6,#fff)" role="img" aria-label="Cross-shaped floral wreath of white and red flowers"></div>
<div class="abs gallery-item" style="left:420px;background:linear-gradient(#c9c2c0,#7c8ea0,#4f6a7a)" role="img" aria-label="Family embracing on rocks by the sea"></div>
<div class="abs gallery-item" style="left:573px;background:linear-gradient(90deg,#dfe3d6,#f4f4f0,#a9b28e)" role="img" aria-label="Mourners in white placing flowers at a memorial"></div>
<div class="abs gallery-item" style="left:726px;background:linear-gradient(#3c5230,#556a3d,#9a5a3a)" role="img" aria-label="Women tending flowers at a grave in a cemetery"></div>

<footer class="abs footer"></footer>
<div class="abs footer-links">HOME | ABOUT | SERVICE | RESOURCES | &nbsp;CONTACT US | SYDNEY</div>
<div class="abs copyright">Copyright © 2013 Reel Harbor. All Rights Reserved.</div>
<div class="abs social"><i style="background:#3b5998"></i><i style="background:#3fa9e0"></i><i style="background:#1f7bb6"></i><i style="background:#f39a1e"></i></div>
</body>
</html>
```